Larkspur Talent IT Recruiting firm needs a business card design for Recruiters, Sourcers, and Account

We need business cards that allow us to change all contact info, names, titles (Recruiter, Sourcer, Account Manager, Director, CEO, etc) per person since we have three offices, in three cities, Phoenix, Austin, and Las Vegas. We do recruiting and contractors for IT positions (Developers, Architects, Software Engineers, Security Engineers, Help Desk, DBAs, PMs, Scrum Masters, etc.) Our client companies are very diverse from Meridian 100 to silicone Valley type start-ups.

So, while we what hip, techie, and quirky, it still needs to be professional. Primary color we use is blue, with silver as a secondary color.

Target Market(s)

IT, Technology

Industry/Entity Type

Business

Contact Information for Business Card

Company name: Larkspur Talent, Inc.
Website: www.larkspurtalent.example
Logos for Careerloop, Blipster, and Myriada

Name, Title, Office Number, Cell Number, email

Font styles to use
Serif
Sans Serif

Colors
0455a3
d5d5d5

Requirements
Nice to have
• The grey I selected below is not necessary - but, would like silver included. I included a card design (File 3: LTI early trial example.jpg) that I had started on. It's very rough, and not quite what we're looking for, but what we did like is the logo, big, maybe a bit faded, off center, goes out of frame, etc. Still looking for other ideas - you are the pros! But, just an idea of a design element we liked.

```html
<!DOCTYPE html>
<html lang="en">
<head>
<meta charset="utf-8">
<title>Larkspur Talent — Business Card</title>
<link rel="stylesheet" href="https://fonts.googleapis.com/css2?family=Cinzel:wght@400;500&family=Open+Sans:wght@400;700&display=swap">
<style>
  :root {
    --brand-blue: #0455a3;
    --silver: #d5d5d5;
    --ink: #2b2b2b;
    --ink-soft: #444;
    --paper: #ffffff;
    --backdrop: #ecebe8;
  }
  * { margin: 0; padding: 0; box-sizing: border-box; }
  html, body {
    width: 1200px; height: 1095px; overflow: hidden;
    background: var(--backdrop);
  }
  .canvas { position: relative; width: 1200px; height: 1095px; }

  .card {
    position: absolute; overflow: hidden;
    box-shadow: 0 4px 14px rgba(0,0,0,.18);
  }
  .card--front { left: 53px; top: 40px; width: 842px; height: 482px; background: var(--paper); }
  .card--back { left: 305px; top: 551px; width: 838px; height: 481px; background: var(--brand-blue); }

  /* Front: brand block */
  .brand {
    position: absolute; left: 44px; top: 146px; width: 382px;
    display: flex; align-items: center; justify-content: space-between;
  }
  .brand__dot { width: 78px; height: 78px; border-radius: 50%; background: var(--brand-blue); flex: none; }
  .brand__name {
    font-family: "Cinzel", serif; font-weight: 500; font-size: 38px; line-height: 1.08;
    letter-spacing: 4px; color: var(--ink); text-align: right;
  }
  .tagline {
    position: absolute; left: 44px; top: 262px; width: 382px; text-align: center;
    font-family: "Cinzel", serif; font-size: 18px; letter-spacing: 2.5px; color: var(--ink-soft);
    white-space: nowrap;
  }
  .divider { position: absolute; left: 472px; top: 106px; width: 2px; height: 208px; background: var(--silver); }

  /* Front: person */
  .person { position: absolute; left: 506px; top: 98px; font-family: "Open Sans", sans-serif; }
  .person__name { font-weight: 700; font-size: 30px; color: var(--brand-blue); line-height: 1.2; }
  .person__title { font-size: 20px; color: var(--ink-soft); margin-top: 6px; }
  .contact { list-style: none; margin-top: 28px; }
  .contact__item { display: flex; align-items: center; gap: 10px; font-size: 19px; color: var(--ink); height: 36px; white-space: nowrap; }
  .contact__icon { width: 18px; height: 18px; flex: none; }

  /* Front: wave band */
  .wave { position: absolute; left: 0; bottom: 0; width: 842px; height: 150px; }
  .social { position: absolute; left: 147px; top: 406px; list-style: none; font-family: "Open Sans", sans-serif; }
  .social__item { display: flex; align-items: center; gap: 8px; color: var(--paper); font-size: 17px; height: 29px; }
  .social__dot { width: 20px; height: 20px; border-radius: 50%; background: var(--paper); flex: none; }

  /* Back */
  .back-brand {
    position: absolute; left: 0; right: 0; top: 120px;
    display: flex; justify-content: center; align-items: center; gap: 28px;
  }
  .back-brand__dot { width: 150px; height: 150px; border-radius: 50%; background: var(--paper); flex: none; }
  .back-brand__name {
    font-family: "Cinzel", serif; font-weight: 500; font-size: 44px; letter-spacing: 5px;
    line-height: 1.08; color: var(--paper);
  }
  .back-url {
    position: absolute; left: 0; right: 0; top: 402px; text-align: center;
    font-family: "Open Sans", sans-serif; font-size: 24px; letter-spacing: 3px; color: var(--paper);
  }
</style>
</head>
<body>
<main class="canvas">

  <section class="card card--front" aria-label="Business card front">
    <div class="brand">
      <span class="brand__dot"></span>
      <div class="brand__name">LARKSPUR<br>TALENT</div>
    </div>
    <p class="tagline">ROOTED IN THE RIGHT FIT</p>
    <span class="divider"></span>

    <div class="person">
      <h1 class="person__name">Maren Ellison</h1>
      <p class="person__title">First Touch Embassador</p>
      <ul class="contact">
        <li class="contact__item">
          <svg class="contact__icon" viewBox="0 0 20 20"><circle cx="10" cy="10" r="9" fill="none" stroke="#0455a3" stroke-width="1.6"/><path d="M7 5.5l2 2-1.2 1.3a6 6 0 0 0 3.4 3.4L12.5 11l2 2-1.3 1.5C9.5 14 6 10.5 5.5 6.8z" fill="#0455a3"/></svg>
          512-555-0147
        </li>
        <li class="contact__item">
          <svg class="contact__icon" viewBox="0 0 20 20"><circle cx="10" cy="10" r="9.5" fill="#0455a3"/><path d="M5 7.5h10v6H5z" fill="#fff"/><path d="M5 7.5l5 3.5 5-3.5" fill="none" stroke="#0455a3" stroke-width="1.2"/></svg>
          maren@larkspurtalent.example
        </li>
        <li class="contact__item">
          <svg class="contact__icon" viewBox="0 0 20 20" fill="none" stroke="#0455a3" stroke-width="1.5"><circle cx="10" cy="10" r="8.5"/><ellipse cx="10" cy="10" rx="3.8" ry="8.5"/><path d="M1.5 10h17M3 5.5h14M3 14.5h14"/></svg>
          www.larkspurtalent.example
        </li>
      </ul>
    </div>

    <svg class="wave" viewBox="0 0 842 150" preserveAspectRatio="none" aria-hidden="true">
      <defs>
        <linearGradient id="silverSweep" x1="0" x2="1">
          <stop offset="0" stop-color="#c9c9c9"/>
          <stop offset=".5" stop-color="#f2f2f2"/>
          <stop offset="1" stop-color="#8f8f8f"/>
        </linearGradient>
      </defs>
      <path d="M0 38 C180 -5 380 0 520 40 C640 75 760 70 842 48 V150 H0Z" fill="url(#silverSweep)"/>
      <path d="M0 50 C190 8 380 14 520 52 C640 86 760 82 842 62 V150 H0Z" fill="#fff"/>
      <path d="M0 62 C200 22 390 30 520 66 C650 102 770 96 842 78 V150 H0Z" fill="#0455a3"/>
      <path d="M470 58 C620 100 760 96 842 70" fill="none" stroke="#d5d5d5" stroke-width="4"/>
    </svg>

    <ul class="social">
      <li class="social__item"><span class="social__dot"></span>@MarenEllisonLT</li>
      <li class="social__item"><span class="social__dot"></span>@MarenEllisonLT</li>
    </ul>
  </section>

  <section class="card card--back" aria-label="Business card back">
    <div class="back-brand">
      <span class="back-brand__dot"></span>
      <div class="back-brand__name">LARKSPUR<br>TALENT</div>
    </div>
    <p class="back-url">www.larkspurtalent.example</p>
  </section>

</main>
</body>
</html>
```